Meal Plan Website Needs New Pages Designed

Brightwick Supper Kits is an online, membership based program that delivers weekly meal programs (7 days worth of recipes plus shopping lists) carefully crafted by an expert team of meal planners. All recipes are created to comply with the following macronutrient ratio: 65% healthy fats, 25% lean protein, 10% good carbs.
All recipes are Paleo friendly and a great resource for those individuals who want to correctly implement this type of diet.

We are re-designing our website and need the following pages designed:

· Home page w/ logo
· How it works page
· Get Started! page
· Recipes Page template (these will be the pages on our site that will have recipes)
· Kitchen Essentials Training page (this will be a page with videos and tips + tricks, PDFs, etc)

So 5 total PSDs, 1 for each page.

Target audience: Men and women between the ages of 30 and 60 who want to:
· Eat healthy
· Lose weight
· Follow/Implement the Paleo diet
· Take the guesswork out of preparing delicious AND healthy meals for them and their families
· Know exactly what to eat, what to buy, how to make it

Feelings/Messages we want to communicate through the design:
· “Organic” but elegant look
· Fresh/light/Airy
· Simple but NOT GENERIC
· “I want to get cooking” feeling

Our Stylistic preferences:
· Minimalist with a few bold elements (something in between)
· Easy to visually navigate (enough white space, but not too much)
· There is more to “see” than to “read”

Our Color Preferences:
· Lighter pallet
· Colors that evoke natural woods, granite countertops…
· Stay away from using all dark colors

Our Font Type Preferences:
· Easy to read
· Not more than 3 font types
· Not too rigid
· Not too sophisticated
· Simple with a touch

Examples of Website Designs that we like:
· http://www.dorvanta.com/meal-plans/
· http://grulvix.com/
· https://www.mistobarn.com/

```html
<!DOCTYPE html>
<html lang="en">
<head>
<meta charset="utf-8">
<title>Brightwick Supper Kits</title>
<link href="https://fonts.googleapis.com/css2?family=Oswald:wght@300;400;500&family=Open+Sans:wght@400;600&display=swap" rel="stylesheet">
<style>
:root{
  --wood-light:#e6cd96;
  --wood-dark:#c9a464;
  --brand-red:#b8332a;
  --cream:#fbf6e4;
  --cream-deep:#f5ecd0;
  --paper:#ffffff;
  --ink:#3b3b3b;
  --muted:#6d6d6d;
  --rule:#ddd3b8;
  --footer:#3a3937;
  --footer-text:#cfcac0;
}
*{box-sizing:border-box;margin:0;padding:0}
html,body{width:764px;height:1200px;overflow:hidden}
body{font-family:"Open Sans",Arial,sans-serif;color:var(--ink);background:var(--paper);font-size:8px;line-height:1.45}
.page{position:relative;width:764px;height:1200px}

.site-header{position:absolute;left:0;top:0;width:764px;height:48px;
  background:linear-gradient(180deg,var(--wood-light),var(--wood-dark));}
.brand{position:absolute;left:18px;top:11px;display:flex;align-items:center;gap:8px}
.brand-mark{width:22px;height:22px;border-radius:50%;background:var(--brand-red)}
.brand-name{font-family:"Oswald",Arial,sans-serif;font-weight:500;font-size:19px;color:var(--brand-red);letter-spacing:.2px}
.account-links{position:absolute;right:20px;top:6px;font-size:7px;color:var(--ink);display:flex;gap:10px}
.main-nav{position:absolute;right:20px;top:27px;display:flex;gap:14px;font-family:"Oswald",Arial,sans-serif;font-size:8.5px;letter-spacing:.4px;color:#2e2a24}

.hero{position:absolute;left:0;top:48px;width:764px;height:242px;display:flex;gap:2px;background:#fff}
.hero-photo{flex:1}
.hero-photo.one{background:linear-gradient(135deg,#e9ece6,#c6b9a2 60%,#d97d3a)}
.hero-photo.two{background:linear-gradient(160deg,#e8e4d8,#b7c4c9 55%,#f1efe6)}
.hero-photo.three{background:linear-gradient(150deg,#d8c7a8,#c9cfa9 50%,#c33b2e)}
.arrow{position:absolute;width:22px;height:22px;border-radius:50%;background:rgba(40,40,40,.65);display:flex;align-items:center;justify-content:center}
.hero .arrow{top:110px}
.hero .arrow.prev{left:10px}.hero .arrow.next{right:10px}

.meal-plans{position:absolute;left:0;top:290px;width:764px;height:300px;background:var(--paper)}
.section-title{position:absolute;left:0;top:34px;width:764px;text-align:center;font-family:"Oswald",Arial,sans-serif;font-weight:400;font-size:17px;letter-spacing:2.5px;color:var(--ink)}
.section-title::after{content:"";display:block;width:620px;height:1px;background:var(--rule);margin:10px auto 0}
.plan-cards{position:absolute;left:143px;top:95px;display:flex;gap:14px}
.plan-card{width:150px}
.plan-photo{position:relative;height:150px}
.plan-photo.classic{background:linear-gradient(140deg,#e9c98d,#c98f4c)}
.plan-photo.vegetarian{background:linear-gradient(140deg,#8aa04e,#5f7a2e 60%,#b8743a)}
.plan-photo.seasonal{background:linear-gradient(140deg,#d9a244,#a8652a)}
.plan-label{position:absolute;left:6px;bottom:6px;font-family:"Oswald",Arial,sans-serif;font-size:11px;color:#fff;letter-spacing:.6px}
.plan-card p{margin-top:6px;font-size:7px;color:var(--muted)}
.meal-plans .arrow{top:140px;background:none}
.meal-plans .arrow.prev{left:60px}.meal-plans .arrow.next{right:60px}

.details{position:absolute;left:0;top:590px;width:764px;height:318px;border-top:1px solid var(--rule);border-bottom:1px solid var(--rule)}
.how-it-works{position:absolute;left:40px;top:24px;width:420px}
.details h2{font-family:"Oswald",Arial,sans-serif;font-weight:400;font-size:15px;color:var(--ink)}
.how-body{display:flex;gap:14px;margin-top:14px}
.plate-icon{flex:none;width:46px;height:46px;border-radius:50%;background:var(--ink);display:flex;align-items:center;justify-content:center}
.how-body p{font-size:7px;color:var(--muted)}
.newsletter{position:absolute;left:40px;top:190px;width:420px}
.newsletter .lead{font-size:7px;color:var(--muted);margin-top:4px}
.signup{display:flex;margin-top:10px;width:230px;height:20px}
.signup .field{flex:1;border:1px solid #bdb7a6;font-size:7px;color:#999;padding:4px 6px}
.signup .go{width:20px;background:var(--ink);display:flex;align-items:center;justify-content:center}
.ratios{position:absolute;left:497px;top:18px;width:240px;display:flex;flex-direction:column;gap:10px}
.ratio{background:var(--cream);padding:14px 16px;height:88px}
.ratio h3{font-family:"Oswald",Arial,sans-serif;font-weight:300;font-size:22px;color:var(--ink)}
.ratio h3 span{font-size:13px;letter-spacing:.8px;margin-left:4px}
.ratio p{font-size:7px;color:var(--muted);margin-top:4px}

.welcome{position:absolute;left:0;top:908px;width:764px;height:242px;background:var(--cream-deep)}
.welcome-art{position:absolute;left:22px;top:14px;width:228px;height:226px;background:linear-gradient(160deg,#f4e6da,#e3b9a6 55%,#c9564a)}
.welcome-text{position:absolute;left:272px;top:26px;width:460px}
.welcome-text h2{font-family:"Oswald",Arial,sans-serif;font-weight:400;font-size:16px;color:var(--ink);margin-bottom:8px}
.welcome-text p{font-size:7px;color:var(--muted);margin-bottom:6px}
.welcome-text p.intro{color:var(--ink);font-weight:600}
.read-more{display:inline-block;margin-top:4px;background:var(--brand-red);color:#fff;font-size:7px;padding:4px 9px}

.site-footer{position:absolute;left:0;top:1150px;width:764px;height:50px;background:var(--footer);color:var(--footer-text);font-size:7px}
.connect{position:absolute;left:40px;top:10px}
.social{display:flex;gap:5px;margin-top:5px}
.social span{width:14px;height:14px;background:#6f6c66}
.footer-nav{position:absolute;right:30px;top:10px;display:flex;gap:10px;font-size:7px;color:#eee}
.copyright{position:absolute;right:30px;top:27px}
</style>
</head>
<body>
<div class="page">
  <header class="site-header">
    <div class="brand"><span class="brand-mark"></span><span class="brand-name">Brightwick Supper Kits</span></div>
    <div class="account-links"><span>Support</span><span>Login</span><span>Register</span></div>
    <nav class="main-nav"><span>HOME</span><span>ABOUT</span><span>MEAL PLANS</span><span>HOW IT WORKS</span><span>BLOG</span><span>CONTACT US</span></nav>
  </header>

  <section class="hero">
    <div class="hero-photo one" role="img" aria-label="Plated roast chicken with carrots and greens"></div>
    <div class="hero-photo two" role="img" aria-label="Bowl of potatoes on a kitchen table"></div>
    <div class="hero-photo three" role="img" aria-label="Fresh vegetables being chopped on a board"></div>
    <span class="arrow prev"><svg width="8" height="10"><path d="M6 1 2 5l4 4" fill="none" stroke="#fff" stroke-width="1.6"/></svg></span>
    <span class="arrow next"><svg width="8" height="10"><path d="M2 1l4 4-4 4" fill="none" stroke="#fff" stroke-width="1.6"/></svg></span>
  </section>

  <section class="meal-plans">
    <h2 class="section-title">MEAL PLANS</h2>
    <span class="arrow prev"><svg width="10" height="14"><path d="M8 1 2 7l6 6" fill="none" stroke="#444" stroke-width="1.8"/></svg></span>
    <div class="plan-cards">
      <article class="plan-card">
        <div class="plan-photo classic" role="img" aria-label="Pasta dish"><span class="plan-label">CLASSIC</span></div>
        <p>Hearty family dinners with balanced fats and lean cuts for every night.</p>
      </article>
      <article class="plan-card">
        <div class="plan-photo vegetarian" role="img" aria-label="Vegetable pasta dish"><span class="plan-label">VEGETARIAN</span></div>
        <p>Colorful plant forward recipes packed with greens, nuts and good oils.</p>
      </article>
      <article class="plan-card">
        <div class="plan-photo seasonal" role="img" aria-label="Roasted corn and grain dish"></div>
        <p>Seasonal weekly menus built around fresh produce from local farms.</p>
      </article>
    </div>
    <span class="arrow next"><svg width="10" height="14"><path d="M2 1l6 6-6 6" fill="none" stroke="#444" stroke-width="1.8"/></svg></span>
  </section>

  <section class="details">
    <div class="how-it-works">
      <h2>How it works</h2>
      <div class="how-body">
        <span class="plate-icon"><svg width="30" height="30" viewBox="0 0 30 30"><circle cx="15" cy="15" r="9" fill="none" stroke="#fff" stroke-width="1.6"/><path d="M3 6v8M5 6v8M4 14v11M27 6c-2 2-2 7 0 9v10" fill="none" stroke="#fff" stroke-width="1.4"/></svg></span>
        <p>Every week our team of meal planners prepares seven days of recipes along with a complete shopping list. Simply log in, choose your plan and download the week's menu. Each recipe follows our macronutrient ratio, so you never have to count or guess. Shop once, cook with confidence and enjoy fresh, nourishing meals with the whole family. Swap recipes you do not like, save your favorites and print tidy lists sorted by store aisle to make shopping quick and simple.</p>
      </div>
    </div>
    <div class="newsletter">
      <h2>Get our newsletter</h2>
      <p class="lead">Keep up to date with fresh new recipes, tips and offers.</p>
      <div class="signup"><span class="field">Enter Email Id</span><span class="go"><svg width="6" height="8"><path d="M1 0l5 4-5 4z" fill="#fff"/></svg></span></div>
    </div>
    <div class="ratios">
      <div class="ratio"><h3>65%<span>Healthy Fats</span></h3><p>Avocado, olive oil, nuts and seeds keep you full and energized.</p></div>
      <div class="ratio"><h3>25%<span>Lean Protein</span></h3><p>Grass fed meats, wild fish and eggs in every weekly plan.</p></div>
      <div class="ratio"><h3>10%<span>Good Carbs</span></h3><p>Fresh vegetables and fruit for fiber and steady energy.</p></div>
    </div>
  </section>

  <section class="welcome">
    <div class="welcome-art" role="img" aria-label="Stack of printed weekly meal plan sheets"></div>
    <div class="welcome-text">
      <h2>Welcome to our site</h2>
      <p class="intro">We believe healthy eating should be simple, delicious and stress free. Our weekly plans take the guesswork out of dinner so you can spend less time planning and more time at the table.</p>
      <p>Each plan includes seven days of recipes, a sorted shopping list and prep notes for busy evenings. Every dish is Paleo friendly and built around wholesome ingredients you can find at any grocery store.</p>
      <p>Whether you want to lose weight, feel better or cook for your family, our planners do the hard work for you. Join today and get cooking.</p>
      <span class="read-more">Read More</span>
    </div>
  </section>

  <footer class="site-footer">
    <div class="connect">Connect with us<div class="social"><span></span><span></span><span></span></div></div>
    <nav class="footer-nav"><span>HOME</span><span>ABOUT</span><span>MEAL PLANS</span><span>HOW IT WORKS</span><span>BLOG</span><span>CONTACT US</span></nav>
    <div class="copyright">Copyrights © 2014 All Rights Reserved</div>
  </footer>
</div>
</body>
</html>
```